business card for a massage therapy practice named 'Cedar and Willow Massage Studio'

I really need a trendy, yet easy on the eyes business card to complement my logo. Ideally with some gold or rose gold foil work.

My uploaded file of the logo I have in horizontal but I have a vertical version as well. Another color that is used in the website is a blush pink here and there. I'd like to see some trendy tropical leaves in the design.

```html
<!DOCTYPE html>
<html lang="en">
<head>
<meta charset="utf-8">
<title>Cedar and Willow Massage Studio — Business Card</title>
<link href="https://fonts.googleapis.com/css2?family=Roboto:wght@400;500&display=swap" rel="stylesheet">
<style>
  :root {
    --backdrop: #ebebe8;
    --paper: #f8f7f4;
    --rose-gold: #b5865c;
    --mint-leaf: #6ccaaa;
    --mint-fade: rgba(108, 202, 170, 0);
  }
  * { box-sizing: border-box; margin: 0; padding: 0; }
  html, body {
    width: 966px;
    height: 1200px;
    overflow: hidden;
    background: var(--backdrop);
  }
  .canvas {
    position: relative;
    width: 966px;
    height: 1200px;
    font-family: "Roboto", Arial, sans-serif;
    color: var(--rose-gold);
  }
  .card {
    position: absolute;
    left: 173px;
    width: 620px;
    height: 354px;
    background: var(--paper);
    box-shadow: 0 6px 18px rgba(0, 0, 0, 0.12);
    overflow: hidden;
  }
  .card--front { top: 140px; }
  .card--back { top: 720px; }

  .palm-fronds {
    position: absolute;
    top: 0;
    right: 0;
    width: 360px;
    height: 300px;
    background:
      radial-gradient(ellipse at 85% 20%, var(--mint-leaf) 0%, rgba(108,202,170,0.75) 35%, var(--mint-fade) 72%);
  }

  .identity {
    position: absolute;
    left: 48px;
    top: 190px;
  }
  .identity__name {
    font-size: 22px;
    font-weight: 500;
    letter-spacing: 0.2px;
  }
  .identity__role {
    font-size: 15px;
    font-weight: 400;
    margin-top: 4px;
  }

  .contact {
    position: absolute;
    left: 42px;
    top: 258px;
    display: flex;
    align-items: center;
  }
  .contact__list {
    list-style: none;
    font-size: 14px;
    line-height: 20px;
  }
  .contact__item {
    display: flex;
    align-items: center;
    gap: 7px;
  }
  .contact__icon { width: 11px; height: 11px; fill: var(--rose-gold); flex: none; }
  .contact__divider {
    width: 1.5px;
    height: 56px;
    background: var(--rose-gold);
    margin: 0 12px 0 12px;
  }
  .contact__address {
    font-size: 14px;
    line-height: 20px;
    font-style: normal;
    padding-top: 16px;
  }

  .brand {
    position: absolute;
    inset: 0;
    display: flex;
    align-items: center;
    justify-content: center;
    gap: 14px;
  }
  .brand__dot {
    width: 40px;
    height: 40px;
    border-radius: 50%;
    background: var(--rose-gold);
  }
  .brand__name {
    font-size: 28px;
    font-weight: 500;
    color: var(--rose-gold);
    letter-spacing: 0.5px;
  }
</style>
</head>
<body>
<main class="canvas">

  <section class="card card--front" aria-label="Card front">
    <div class="palm-fronds" role="img" aria-label="Mint green tropical palm fronds reaching in from the top right corner"></div>

    <div class="identity">
      <h1 class="identity__name">Marisol Vega</h1>
      <p class="identity__role">Massage Therapist</p>
    </div>

    <div class="contact">
      <ul class="contact__list">
        <li class="contact__item">
          <svg class="contact__icon" viewBox="0 0 24 24" aria-hidden="true"><path d="M6.6 10.8c1.4 2.8 3.8 5.1 6.6 6.6l2.2-2.2c.3-.3.7-.4 1-.2 1.1.4 2.3.6 3.6.6.6 0 1 .4 1 1V20c0 .6-.4 1-1 1C10.6 21 3 13.4 3 4c0-.6.4-1 1-1h3.5c.6 0 1 .4 1 1 0 1.3.2 2.5.6 3.6.1.3 0 .7-.2 1L6.6 10.8z"/></svg>
          (916) 555-0142
        </li>
        <li class="contact__item">
          <svg class="contact__icon" viewBox="0 0 24 24" aria-hidden="true"><path d="M2 5h20v14H2z M2 5l10 7 10-7" fill="var(--rose-gold)"/><path d="M3 6l9 6.3L21 6" fill="none" stroke="#f8f7f4" stroke-width="1.6"/></svg>
          info@cedarandwillow.com
        </li>
        <li class="contact__item">
          <svg class="contact__icon" viewBox="0 0 24 24" aria-hidden="true"><circle cx="12" cy="12" r="10"/><path d="M2 12h20M12 2c3 3 3 17 0 20M12 2c-3 3-3 17 0 20" fill="none" stroke="#f8f7f4" stroke-width="1.5"/></svg>
          www.cedarandwillow.com
        </li>
      </ul>
      <span class="contact__divider" aria-hidden="true"></span>
      <address class="contact__address">
        482 Laurel Ave #210<br>
        Sacramento, CA 95816
      </address>
    </div>
  </section>

  <section class="card card--back" aria-label="Card back">
    <div class="brand">
      <span class="brand__dot" aria-hidden="true"></span>
      <span class="brand__name">Cedar and Willow Massage Studio</span>
    </div>
  </section>

</main>
</body>
</html>
```